Business cards to launch an education platform

Hi,
I am looking at having new business cards designed.
I am a startup, developing a web platform for schools and university, the education world. It's an online assessment system.
I would like a card that looks classy, and that is using the colors and the font of my logo.

I have attached:
1) my logo
2) A business card that I have designed quickly so you can have all the information required in the card, but I really don't like it.
3) The font that I am using (Lato Regular) to design my web platform
4) Some screenshots of my web platform so you can have a look at the style that I have.

Target Market(s)

Major market: Education system: Schools and university
Minor markets: Business in general

Industry/Entity Type

Business

Contact Information for Business Card

Clara Fenwick
Director

M: 0437 518 902
E: clara.fenwick@amberLoomSystems.com.au

Requirements
Must have
• The colors of my logo

```html
<!DOCTYPE html>
<html lang="en">
<head>
<meta charset="utf-8">
<title>Amber Loom Systems — Business Cards</title>
<link rel="stylesheet" href="https://fonts.googleapis.com/css2?family=Lato:wght@400&display=swap">
<style>
  :root {
    --page-bg: #d9d9d7;
    --card-bg: #141414;
    --card-bg-edge: #0b0b0b;
    --brand-blue: #2f86cf;
    --accent-blue: #37aee6;
    --text-light: #e6e6e6;
    --text-muted: #bdbdbd;
    --rule: #2c2c2c;
  }
  * { box-sizing: border-box; margin: 0; padding: 0; }
  html, body {
    width: 1200px;
    height: 900px;
    overflow: hidden;
  }
  body {
    background: var(--page-bg);
    font-family: "Lato", sans-serif;
    display: flex;
    flex-direction: column;
    align-items: center;
    justify-content: center;
    gap: 40px;
  }
  .card {
    position: relative;
    width: 640px;
    height: 391px;
    background: radial-gradient(ellipse at 60% 40%, var(--card-bg) 0%, var(--card-bg-edge) 100%);
    box-shadow: 0 6px 18px rgba(0, 0, 0, 0.25);
    overflow: hidden;
  }

  /* Logo side */
  .card--brand {
    display: flex;
    align-items: center;
    justify-content: center;
    gap: 22px;
  }
  .brand-mark {
    width: 70px;
    height: 70px;
    background: var(--brand-blue);
    flex: none;
  }
  .brand-name {
    color: var(--brand-blue);
    font-size: 34px;
    letter-spacing: 3px;
    line-height: 1.1;
  }

  /* Contact side */
  .contact-brand {
    position: absolute;
    top: 112px;
    right: 180px;
    text-align: right;
    color: var(--brand-blue);
    font-size: 27px;
    letter-spacing: 2.5px;
    line-height: 1.2;
  }
  .contact-divider {
    position: absolute;
    top: 100px;
    left: 480px;
    width: 1.5px;
    height: 98px;
    background: var(--accent-blue);
  }
  .contact-mark {
    position: absolute;
    top: 116px;
    left: 506px;
    width: 72px;
    height: 72px;
    background: var(--brand-blue);
  }
  .person {
    position: absolute;
    top: 148px;
    left: 40px;
  }
  .person-name {
    color: var(--accent-blue);
    font-size: 23px;
    line-height: 1.1;
  }
  .person-role {
    color: var(--text-muted);
    font-size: 14px;
    margin-top: 2px;
  }
  .contact-rule {
    position: absolute;
    top: 222px;
    left: 40px;
    width: 560px;
    height: 1px;
    background: var(--rule);
  }
  .contact-details {
    position: absolute;
    right: 40px;
    bottom: 46px;
    list-style: none;
    text-align: right;
    color: var(--text-light);
    font-size: 16px;
    line-height: 1.6;
  }
  .contact-details li {
    display: flex;
    align-items: center;
    justify-content: flex-end;
    gap: 12px;
  }
  .contact-icon {
    width: 13px;
    height: 13px;
    fill: var(--accent-blue);
    flex: none;
  }
</style>
</head>
<body>

  <section class="card card--brand" aria-label="Business card, logo side">
    <div class="brand-mark" aria-hidden="true"></div>
    <p class="brand-name">Amber Loom Systems</p>
  </section>

  <section class="card card--contact" aria-label="Business card, contact side">
    <p class="contact-brand">Amber Loom<br>Systems</p>
    <div class="contact-divider" aria-hidden="true"></div>
    <div class="contact-mark" aria-hidden="true"></div>

    <div class="person">
      <p class="person-name">Clara Fenwick</p>
      <p class="person-role">Director</p>
    </div>

    <div class="contact-rule" aria-hidden="true"></div>

    <ul class="contact-details">
      <li>0437 518 902
        <svg class="contact-icon" viewBox="0 0 24 24" aria-hidden="true">
          <path d="M6.6 10.8a15.1 15.1 0 0 0 6.6 6.6l2.2-2.2a1 1 0 0 1 1-.25 11.4 11.4 0 0 0 3.6.57 1 1 0 0 1 1 1V20a1 1 0 0 1-1 1A17 17 0 0 1 3 4a1 1 0 0 1 1-1h3.5a1 1 0 0 1 1 1c0 1.25.2 2.45.57 3.6a1 1 0 0 1-.25 1z"/>
        </svg>
      </li>
      <li>clara.fenwick@amberLoomSystems.com.au
        <svg class="contact-icon" viewBox="0 0 24 24" aria-hidden="true">
          <path d="M2 5h20v14H2z M2 5l10 8 10-8" fill="var(--accent-blue)" stroke="var(--card-bg)" stroke-width="1.5"/>
        </svg>
      </li>
    </ul>
  </section>

</body>
</html>
```